professional business card design

Business card design. Photos have been uploaded and i am open to the designer choosing which photos to use. Would like the card to be mostyly in a grey scale design with black, whites, silver & grey colours. I have added copy of our flyer as would like on the back side of card our services to be listed. Do not use any bright colurs such as blue red green or yellow. i need to be able to edit the phone number and naem in the final card design submitted.

Target Market(s)

Clients

Industry/Entity Type

earhmovibng and transport

Contact Information for Business Card

Director Name, address, email, phone number and services

Colors

Designer to choose only greyscale colors for use in the design.

Requirements
Should not have
• no yellow, red, blue or green

```html
<!DOCTYPE html>
<html lang="en">
<head>
<meta charset="utf-8">
<title>Zarvell Haulage – Business Card</title>
<link href="https://fonts.googleapis.com/css2?family=Lato:wght@400;700;900&display=swap" rel="stylesheet">
<style>
  :root {
    --bg: #1b1b1c;
    --card: #0c0c0d;
    --card-edge: #2a2a2c;
    --panel: #262628;
    --silver: #c9c9cc;
    --silver-light: #ececee;
    --white: #ffffff;
    --photo-dark: #121213;
    --photo-mid: #4a4a4c;
  }
  * { box-sizing: border-box; margin: 0; padding: 0; }
  html, body { width: 1200px; height: 800px; overflow: hidden; }
  body {
    background: var(--bg);
    font-family: "Lato", sans-serif;
    position: relative;
  }
  .card {
    position: absolute;
    top: 235px;
    width: 540px;
    height: 330px;
    border-radius: 22px;
    background: var(--card);
    overflow: hidden;
    box-shadow: 0 0 0 1px var(--card-edge);
  }
  .card--front { left: 30px; }
  .card--back { left: 630px; }

  /* Brand block: name with a plain dot, descriptor line below */
  .brand {
    position: absolute;
    color: var(--silver-light);
    display: flex;
    flex-direction: column;
    line-height: 1;
  }
  .brand__name {
    display: flex; align-items: center; gap: 10px;
    font-weight: 900; letter-spacing: 2px; white-space: nowrap;
  }
  .brand__dot { width: 14px; height: 14px; border-radius: 50%; background: var(--silver); flex: none; }
  .brand__suffix {
    margin-top: 8px;
    font-size: 14px; font-weight: 900; letter-spacing: 1px;
    color: var(--silver-light);
    padding-left: 24px;
  }

  /* Front */
  .front__panel {
    position: absolute; inset: 0;
    background: linear-gradient(160deg, var(--panel) 0%, #151516 70%);
    clip-path: polygon(0 0, 62% 0, 42% 100%, 0 100%);
  }
  .front__photo {
    position: absolute; top: 0; right: 0; bottom: 0; width: 62%;
    background: radial-gradient(ellipse at 55% 50%, var(--photo-mid) 0%, #2b2b2c 40%, var(--photo-dark) 80%);
    clip-path: polygon(32% 0, 100% 0, 100% 100%, 0 100%);
  }
  .front__divider { position: absolute; inset: 0; width: 100%; height: 100%; }
  .front .brand { left: 30px; top: 44px; }
  .front .brand__name { font-size: 32px; }

  .contact { position: absolute; left: 30px; top: 150px; color: var(--white); }
  .contact__name { font-size: 22px; font-weight: 700; letter-spacing: 1px; color: var(--silver); line-height: 26px; }
  .contact__title { font-size: 15px; color: var(--silver); margin-bottom: 12px; }
  .contact__row { display: flex; align-items: flex-start; gap: 9px; font-size: 13px; line-height: 17px; color: var(--silver); margin-bottom: 6px; }
  .contact__row--phone { font-size: 16px; font-weight: 700; color: var(--white); }
  .contact__row svg { flex: none; margin-top: 2px; }

  /* Back */
  .back__pattern {
    position: absolute; inset: 0;
    background: linear-gradient(180deg, #2c2c2e 0%, #1a1a1b 45%, var(--card) 75%);
  }
  .back__photo {
    position: absolute; left: 0; right: 0; bottom: 0; height: 62%;
    background: linear-gradient(180deg, rgba(60,60,62,0) 0%, rgba(70,70,72,0.55) 35%, rgba(30,30,31,0.8) 65%, var(--card) 100%);
  }
  .back .brand { left: 50%; top: 56px; transform: translateX(-50%); align-items: center; }
  .back .brand__name { font-size: 38px; }
  .back .brand__suffix { padding-left: 24px; }

  .services {
    position: absolute; left: 10px; right: 10px; bottom: 30px;
    list-style: none;
    color: var(--white); font-size: 14px; line-height: 22px;
  }
  .services li { display: flex; justify-content: center; align-items: center; gap: 6px; white-space: nowrap; }
  .tick { width: 13px; height: 13px; flex: none; }
</style>
</head>
<body>

<svg width="0" height="0" style="position:absolute">
  <defs>
    <symbol id="icon-tick" viewBox="0 0 16 16">
      <circle cx="8" cy="8" r="8" fill="#ffffff"/>
      <path d="M4.3 8.3 L7 10.8 L11.8 5.4" fill="none" stroke="#111" stroke-width="2" stroke-linecap="round" stroke-linejoin="round"/>
    </symbol>
  </defs>
</svg>

<section class="card card--front front">
  <div class="front__panel" role="img" aria-label="Dark perforated metal texture"></div>
  <div class="front__photo" role="img" aria-label="Photo of a road train truck cab at night"></div>
  <svg class="front__divider" viewBox="0 0 540 330" aria-hidden="true">
    <line x1="334" y1="0" x2="227" y2="330" stroke="#d8d8da" stroke-width="4"/>
  </svg>

  <div class="brand">
    <span class="brand__name"><span class="brand__dot"></span>ZARVELL</span>
    <span class="brand__suffix">Haulage</span>
  </div>

  <div class="contact">
    <p class="contact__name">MICHAEL SMITH</p>
    <p class="contact__title">Director &amp; Founder</p>
    <div class="contact__row">
      <svg width="11" height="14" viewBox="0 0 12 16"><path d="M6 0a6 6 0 0 0-6 6c0 4.5 6 10 6 10s6-5.5 6-10a6 6 0 0 0-6-6zm0 8.5A2.5 2.5 0 1 1 6 3.5a2.5 2.5 0 0 1 0 5z" fill="#c9c9cc"/></svg>
      <span>Your Address, City<br>State, Zip 1235</span>
    </div>
    <div class="contact__row contact__row--phone">
      <svg width="13" height="13" viewBox="0 0 16 16"><path d="M3.6 0.8l2.3 2.3-1.4 2.1c.9 2 2.4 3.5 4.4 4.4l2.1-1.4 2.3 2.3-1.6 2.9C6.6 13.3 2.7 9.4 0.7 4.3z" fill="#c9c9cc"/></svg>
      <span>(123) 456-7890</span>
    </div>
    <div class="contact__row">
      <svg width="13" height="10" viewBox="0 0 16 12"><rect x="0.5" y="0.5" width="15" height="11" fill="#c9c9cc"/><path d="M0.5 0.5 L8 7 L15.5 0.5" fill="none" stroke="#0c0c0d" stroke-width="1.2"/></svg>
      <span>info@yourwebsite.com</span>
    </div>
  </div>
</section>

<section class="card card--back back">
  <div class="back__pattern" role="img" aria-label="Dark perforated metal texture"></div>
  <div class="back__photo" role="img" aria-label="Greyscale photo of a road train with tipper trailers"></div>

  <div class="brand">
    <span class="brand__name"><span class="brand__dot"></span>ZARVELL</span>
    <span class="brand__suffix">Haulage</span>
  </div>

  <ul class="services">
    <li>Over Size Loads / Hot Shot Loads</li>
    <li>Heavy Vehicle Recovery Services <svg class="tick"><use href="#icon-tick"/></svg> Poatable Water Deliveries</li>
    <li>Road Building / Maintenance <svg class="tick"><use href="#icon-tick"/></svg> Earthworks <svg class="tick"><use href="#icon-tick"/></svg> Sand &amp; Metal Supply &amp; Cartage</li>
    <li>Road Train Tippers <svg class="tick"><use href="#icon-tick"/></svg> Road Train Tankers <svg class="tick"><use href="#icon-tick"/></svg> Road Train Flat Tops</li>
    <li>Drop Dect Trailers <svg class="tick"><use href="#icon-tick"/></svg> Mine Site Accredited Equipment and Operators</li>
  </ul>
</section>

</body>
</html>
```